Professional Package for CPA Firm

We would like a stationery design for our new CPA Firm based in Atlanta, GA called 'Vale 8'. We work with investors to help grow investments, tax free. We would like the design to have a professional/minimal look with a 'wow' factor. We need 9.5″ x 4.125″, 9x12, and 10x13 mailing envelopes, business cards, and a letterhead. We have a logo that is already complete. For the letterhead, we would like to have space to put credentials at the bottom of the page

Industry/Entity Type

CPA, Accounting

```html
<!DOCTYPE html>
<html lang="en">
<head>
<meta charset="utf-8">
<title>Vale 8 — Stationery Package</title>
<link href="https://fonts.googleapis.com/css2?family=Lato:wght@300;400;700;900&family=Allura&display=swap" rel="stylesheet">
<style>
  :root{
    --stage:#9a9a9a;
    --paper:#ffffff;
    --ink:#1c1c1c;
    --muted:#4a4a4a;
    --black:#000000;
    --blue:#0b9bd9;
    --sky:#e3f3fb;
    --rule:#bdbdbd;
  }
  *{box-sizing:border-box;margin:0;padding:0}
  html,body{width:1200px;height:680px;overflow:hidden}
  body{background:var(--stage);font-family:"Lato",sans-serif;color:var(--ink);position:relative}
  .piece{position:absolute;background:var(--paper);overflow:hidden;box-shadow:0 1px 3px rgba(0,0,0,.25)}
  .label{position:absolute;font-size:9.5px;letter-spacing:.2px;color:#111;transform:translateX(-50%);white-space:nowrap}
  .wordmark{font-family:"Lato",sans-serif;font-weight:900;letter-spacing:.5px;display:flex;align-items:center;gap:4px;line-height:1}
  .wordmark .dot{display:inline-block;background:var(--blue)}
  .wordmark.light{color:#fff}
  .wordmark.dark{color:var(--black)}
  .script{font-family:"Allura",cursive}
  .sky-fade{position:absolute;right:0;bottom:0;background:linear-gradient(135deg,rgba(227,243,251,0) 35%,var(--sky) 65%)}
  .blue{color:var(--blue)}
  .contact{list-style:none}
  .contact li{display:flex;align-items:center;gap:4px;white-space:nowrap}
  .contact svg{fill:var(--blue);flex:none}
  .vrule{position:absolute;background:var(--rule);width:1px}

  /* Letterhead */
  .letterhead{left:66px;top:47px;width:390px;height:553px}
  .letterhead .band{height:75px;background:var(--black);position:relative}
  .letterhead .band .wordmark{position:absolute;left:35px;top:30px;font-size:16px}
  .letterhead .band .wordmark .dot{width:7px;height:7px}
  .letterhead .address{position:absolute;right:109px;top:28px;text-align:right;font-size:6.6px;line-height:8.8px;color:#fff}
  .letterhead .band .vrule{left:289px;top:28px;height:24px;background:#666}
  .letterhead .band .contact{position:absolute;left:299px;top:27px;font-size:6.6px;line-height:8.8px;color:#fff}
  .letter{position:absolute;left:35px;top:155px;width:325px}
  .letter .salute{font-size:10px;font-weight:300;color:var(--muted);margin-bottom:18px}
  .letter p{font-size:5.2px;line-height:8.4px;color:var(--muted);margin-bottom:6.5px;text-align:justify}
  .letter .closing{margin-top:14px}
  .signature{position:absolute;left:32px;top:386px;width:70px;height:28px;background:linear-gradient(90deg,#d5e3f5,#eaf1fa);border-radius:3px}
  .letterhead .sky-fade{width:280px;height:200px}
  .letterhead .tagline{position:absolute;left:105px;top:490px;font-size:15px;color:#222}

  /* Envelope */
  .env-back{left:490px;top:47px;width:354px;height:160px}
  .env-back .flap{position:absolute;left:0;top:0;width:354px;height:60px;background:var(--blue);border-radius:0 0 18px 18px;clip-path:polygon(0 0,100% 0,97% 100%,3% 100%)}
  .env-back .tagline{position:absolute;left:0;right:0;top:28px;text-align:center;color:#fff;font-size:10px}
  .env-front{left:544px;top:130px;width:355px;height:163px}
  .env-front .band{height:62px;background:var(--black);position:relative}
  .env-front .band .wordmark{position:absolute;left:18px;top:34px;font-size:12px}
  .env-front .band .wordmark .dot{width:5px;height:5px}
  .env-front .address{position:absolute;left:19px;top:70px;font-size:7px;line-height:9px;color:var(--muted)}
  .env-front .sky-fade{width:160px;height:100px}

  /* Cards */
  .card-front{left:944px;top:48px;width:186px;height:107px}
  .card-front .who{position:absolute;right:93px;top:42px;text-align:right;font-size:3.6px;line-height:5.4px;color:var(--muted)}
  .card-front .who strong{display:block;font-size:5.6px;color:var(--blue);font-weight:700;line-height:6px}
  .card-front .vrule{left:97px;top:41px;height:22px}
  .card-front .contact{position:absolute;left:102px;top:42px;font-size:3.6px;line-height:5.4px;color:var(--muted)}
  .card-back{left:944px;top:182px;width:193px;height:110px;background:var(--black)}
  .card-back .wordmark{position:absolute;left:0;right:0;top:44px;justify-content:center;font-size:15px}
  .card-back .wordmark .dot{width:6px;height:6px}
  .card-back .tagline{position:absolute;left:0;right:0;top:84px;text-align:center;color:#fff;font-size:9px}

  /* Email signatures */
  .sig-one{left:490px;top:334px;width:176px;height:266px}
  .sig-one .wordmark{position:absolute;left:28px;top:70px;font-size:20px}
  .sig-one .wordmark .dot{width:8px;height:8px}
  .sig-one .name{position:absolute;left:27px;top:109px;font-size:15px;font-weight:400}
  .sig-one .title{position:absolute;left:27px;top:126px;font-size:9px}
  .sig-one .dash{position:absolute;left:28px;height:1px;width:14px;background:var(--rule)}
  .sig-one .address{position:absolute;left:28px;top:154px;font-size:9px;line-height:11.5px;color:var(--muted)}
  .sig-one .contact{position:absolute;left:28px;top:194px;font-size:9px;line-height:11.5px;color:var(--muted)}
  .sig-one .sky-fade{width:130px;height:110px}

  .sig-two{left:695px;top:334px;width:455px;height:141px}
  .sig-two .wordmark{position:absolute;left:38px;top:62px;font-size:20px}
  .sig-two .wordmark .dot{width:8px;height:8px}
  .sig-two .vr-a{left:139px;top:48px;height:50px}
  .sig-two .vr-b{left:297px;top:48px;height:50px}
  .sig-two .who{position:absolute;left:162px;top:45px;font-size:9px;line-height:11.5px;color:var(--muted)}
  .sig-two .who .name{font-size:15px;line-height:17px}
  .sig-two .who .title{color:var(--ink);margin-bottom:3px}
  .sig-two .contact{position:absolute;left:318px;top:50px;font-size:9px;line-height:11.5px;color:var(--muted)}
  .sig-two .sky-fade{width:200px;height:120px}

  .sig-three{left:695px;top:513px;width:455px;height:87px}
  .sig-three .wordmark{position:absolute;left:19px;top:40px;font-size:17px}
  .sig-three .wordmark .dot{width:7px;height:7px}
  .sig-three .vrule{top:29px;height:31px}
  .sig-three .who{position:absolute;left:115px;top:33px;width:88px;text-align:center;font-size:9px;line-height:11px}
  .sig-three .who .name{font-size:13.5px;line-height:15px}
  .sig-three .address{position:absolute;left:226px;top:28px;font-size:9px;line-height:11.5px;color:var(--muted)}
  .sig-three .contact{position:absolute;left:350px;top:29px;font-size:9px;line-height:11.5px;color:var(--muted)}
  .sig-three .sky-fade{width:130px;height:80px}
</style>
</head>
<body>

<svg width="0" height="0" style="position:absolute" aria-hidden="true">
  <defs>
    <symbol id="i-phone" viewBox="0 0 10 10"><path d="M2 .8l1.6 2-.9 1.1c.5 1 1.4 1.9 2.4 2.4l1.1-.9 2 1.6-.9 1.6C4.8 8.6 1.4 5.2 1.2 1.7z"/></symbol>
    <symbol id="i-mobile" viewBox="0 0 10 10"><path d="M3 .5h4a.6.6 0 0 1 .6.6v7.8a.6.6 0 0 1-.6.6H3a.6.6 0 0 1-.6-.6V1.1A.6.6 0 0 1 3 .5zm.4 1v6.4h3.2V1.5z"/></symbol>
    <symbol id="i-mail" viewBox="0 0 10 10"><path d="M1 2.5h8v5H1zm.6.6L5 5.6l3.4-2.5z"/></symbol>
    <symbol id="i-web" viewBox="0 0 10 10"><circle cx="5" cy="5" r="4"/></symbol>
  </defs>
</svg>

<!-- Letterhead -->
<section class="piece letterhead">
  <header class="band">
    <div class="wordmark light"><span class="dot"></span>VALE 8</div>
    <div class="address">214 Laurel Court<br>Atlanta, Georgia 30308<br><span class="blue">www.vale8.com</span></div>
    <span class="vrule"></span>
    <ul class="contact">
      <li><svg width="6" height="6"><use href="#i-phone"/></svg>404-555-0137</li>
      <li><svg width="6" height="6"><use href="#i-mobile"/></svg>404-555-0192</li>
      <li><svg width="6" height="6"><use href="#i-mail"/></svg>info@vale8.com</li>
    </ul>
  </header>
  <div class="sky-fade" aria-hidden="true"></div>
  <article class="letter">
    <p class="salute">Dear Mr. Reyes,</p>
    <p>Lorem ipsum dolor sit amet, consectetur adipiscing elit. Donec orci purus, luctus vitae dignissim eu, iaculis sed purus. Vivamus faucibus, ipsum nec aliquet viverra, leo mauris condimentum ligula, sit amet sagittis enim ligula quis arcu. Nam egestas tortor id nisi porttitor mattis. In tortor ante, ultricies in suscipit a, tempus non massa. Vivamus et auctor mi. Fusce vel massa nulla. Phasellus nec eros mauris, et scelerisque orci.</p>
    <p>Donec malesuada orci vitae nulla accumsan porta a id massa. Quisque accumsan iaculis magna sit amet fringilla. Maecenas consequat, magna eget tincidunt semper, odio nibh rutrum mi, id feugiat ante nisi eu risus. Vestibulum nunc orci, rhoncus a placerat in, ultricies in mi. Cras mattis varius eros, vel fringilla nisi suscipit eget. Quisque scelerisque sagittis nulla at porttitor.</p>
    <p>Sed id augue vitae urna euismod commodo aliquet a quam. Pellentesque arcu velit, cursus et malesuada ut, consequat et diam. Nullam erat sem, rhoncus id ullamcorper vitae, rhoncus et arcu. In ultricies ultricies nulla, ut rutrum nisi iaculis at. Donec eu magna a metus ornare faucibus. Fusce aliquet faucibus ultricies. Morbi semper, est id tincidunt gravida, sem arcu adipiscing lacus, ac bibendum nulla leo eu purus. Quisque nec diam sed risus consectetur a cumsan quis quis nibh. Vestibulum id purus lorem.</p>
    <p>It is a long established fact that a reader will be distracted by the readable content of a page when looking at its layout. The point of using Lorem Ipsum is that it has a more-or-less normal distribution of letters, as opposed to using 'Content here, content here', making it look like readable English. Many desktop publishing packages</p>
    <p class="closing">Sincerely,</p>
  </article>
  <div class="signature" role="img" aria-label="Handwritten signature in blue ink"></div>
  <p class="tagline script">Grow Your Investments Tax-Free</p>
</section>
<span class="label" style="left:269px;top:620px">LETTERHEAD</span>

<!-- Envelope -->
<section class="piece env-back">
  <div class="flap"></div>
  <p class="tagline script">Grow Your Investments Tax-Free</p>
</section>
<section class="piece env-front">
  <header class="band">
    <div class="wordmark light"><span class="dot"></span>VALE 8</div>
  </header>
  <p class="address">214 Laurel Court<br>Atlanta, Georgia 30308</p>
  <div class="sky-fade" aria-hidden="true"></div>
</section>
<span class="label" style="left:723px;top:304px">ENVELOPE</span>

<!-- Business cards -->
<section class="piece card-front">
  <div class="who"><strong>DANIEL REYES</strong>President<br>214 Laurel Court<br>Atlanta, Georgia 30308</div>
  <span class="vrule"></span>
  <ul class="contact">
    <li><svg width="3" height="3"><use href="#i-phone"/></svg>404-555-0137</li>
    <li><svg width="3" height="3"><use href="#i-mobile"/></svg>404-555-0164</li>
    <li><svg width="3" height="3"><use href="#i-mail"/></svg>info@vale8.com</li>
    <li><svg width="3" height="3"><use href="#i-web"/></svg>www.vale8.com</li>
  </ul>
</section>
<span class="label" style="left:1040px;top:164px">FRONT CARD</span>

<section class="piece card-back">
  <div class="wordmark light"><span class="dot"></span>VALE 8</div>
  <p class="tagline script">Grow Your Investments Tax-Free</p>
</section>
<span class="label" style="left:1040px;top:304px">BACK CARD</span>

<!-- Email signature 1 -->
<section class="piece sig-one">
  <div class="sky-fade" aria-hidden="true"></div>
  <div class="wordmark dark"><span class="dot"></span>VALE 8</div>
  <p class="name blue">Daniel Reyes</p>
  <p class="title">President</p>
  <span class="dash" style="top:146px"></span>
  <p class="address">214 Laurel Court<br>Atlanta, Georgia 30308</p>
  <span class="dash" style="top:184px"></span>
  <ul class="contact">
    <li><svg width="7" height="7"><use href="#i-phone"/></svg>404-555-0137</li>
    <li><svg width="7" height="7"><use href="#i-mobile"/></svg>404-555-0192</li>
    <li><svg width="7" height="7"><use href="#i-mail"/></svg>info@vale8.com</li>
    <li><svg width="7" height="7"><use href="#i-web"/></svg>www.vale8.com</li>
  </ul>
</section>
<span class="label" style="left:581px;top:620px">EMAIL SIGNATURE 1</span>

<!-- Email signature 2 -->
<section class="piece sig-two">
  <div class="sky-fade" aria-hidden="true"></div>
  <div class="wordmark dark"><span class="dot"></span>VALE 8</div>
  <span class="vrule vr-a"></span>
  <div class="who">
    <p class="name blue">Daniel Reyes</p>
    <p class="title">President</p>
    <p>214 Laurel Court<br>Atlanta, Georgia 30308</p>
  </div>
  <span class="vrule vr-b"></span>
  <ul class="contact">
    <li><svg width="7" height="7"><use href="#i-phone"/></svg>404-555-0137</li>
    <li><svg width="7" height="7"><use href="#i-mobile"/></svg>404-555-0192</li>
    <li><svg width="7" height="7"><use href="#i-mail"/></svg>info@vale8.com</li>
    <li><svg width="7" height="7"><use href="#i-web"/></svg>www.vale8.com</li>
  </ul>
</section>
<span class="label" style="left:909px;top:488px">EMAIL SIGNATURE 2</span>

<!-- Email signature 3 -->
<section class="piece sig-three">
  <div class="sky-fade" aria-hidden="true"></div>
  <div class="wordmark dark"><span class="dot"></span>VALE 8</div>
  <span class="vrule" style="left:101px"></span>
  <div class="who">
    <p class="name blue">Daniel Reyes</p>
    <p>President</p>
  </div>
  <span class="vrule" style="left:211px"></span>
  <p class="address">214 Laurel Court<br>Atlanta, Georgia 30308<br>www.vale8.com</p>
  <span class="vrule" style="left:334px"></span>
  <ul class="contact">
    <li><svg width="7" height="7"><use href="#i-phone"/></svg>404-555-0137</li>
    <li><svg width="7" height="7"><use href="#i-mobile"/></svg>404-555-0192</li>
    <li><svg width="7" height="7"><use href="#i-mail"/></svg>info@vale8.com</li>
  </ul>
</section>
<span class="label" style="left:909px;top:620px">EMAIL SIGNATURE 3</span>

</body>
</html>
```